Very dated, simple professional product website needs updating/reskinning of template

Our client currently has a very simple website at www.brightpitch4homes.example that is very, very dated, uses flash, and the template needs to have an updated look for 2014. It needs to look professional, corporate, strong colors, and if using images, actors must have a very well dressed look, etc. Client likes the layout (but not necessarily the colors, etc.) of another similar product site, www.deedcraftkit.example, for example.

The Keystoner product is an online "presentation document builder" that uses up-to-date content for agents to create 20 - 40 page presentations for potential clients. Real estate agents pay $500+ one-time plus $85/year to use the service, so the website look needs to be consistent with a $500+ product. All of the content will stay essentially the same for now: the goal is to simply re-skin the site to make it look modern, ideally through the use of new CSS files and images, and maybe some script. But we do not want to recode the whole thing, just update the template.

The site layout also needs to work with mobile devices, and so the flash has to be removed, but there is still a need to have possibly a slideshow or something to quickly grab the attention of people who visit the site so they can very quickly understand what the product is.

Also, the plan is to cut down on some of the menu buttons and/or rename them to be more compelling. There are pages on the site that can only be viewed after logging in, and we will want to use the template for those secure pages also.

Project Deadline Extended
Reason: My clients have requested that we see if we can get a few more designs to choose between, and to provide them with some time to mull over the current designs.

Project Deadline Extended
Reason: My client has requested that we continue to seek designs.

Industry/Entity Type

Product

```html
<!DOCTYPE html>
<html lang="en">
<head>
<meta charset="utf-8">
<title>Keystoner 4 Real Estate</title>
<link href="https://fonts.googleapis.com/css2?family=Roboto+Condensed:wght@300;400;700&family=Arimo:wght@400;700&display=swap" rel="stylesheet">
<style>
:root{
  --navy:#123c8c;
  --navy-deep:#0f3584;
  --red:#e8101a;
  --ink:#333333;
  --muted:#666666;
  --soft:#9a9a9a;
  --line:#e4e4e4;
  --white:#ffffff;
  --footer-link:#c9d6f5;
}
*{box-sizing:border-box;margin:0;padding:0}
html,body{width:1200px;height:1080px;overflow:hidden;background:var(--white)}
body{font-family:"Arimo",Arial,sans-serif;color:var(--ink);position:relative}
.top-rule{position:absolute;left:0;top:0;width:1200px;height:4px;background:var(--navy)}
.header{position:absolute;left:0;top:4px;width:1200px;height:136px}
.brand{position:absolute;left:161px;top:28px}
.brand-name{font-family:"Roboto Condensed",sans-serif;font-weight:400;color:var(--navy);line-height:1;white-space:nowrap}
.brand-name .main{display:block;font-size:42px;letter-spacing:.5px}
.brand-name .sub{display:block;font-size:18px;margin-top:4px;padding-left:2px}
.help{position:absolute;right:161px;top:22px;text-align:right}
.help-label{font-size:14px;color:var(--soft);display:flex;align-items:center;justify-content:flex-end;gap:6px}
.help-phone{font-family:"Roboto Condensed",sans-serif;font-size:21px;color:var(--red);margin-top:2px}
.account{position:absolute;right:161px;top:80px;display:flex;align-items:center;gap:8px;font-size:12px}
.icon-ring{width:27px;height:27px;border-radius:50%;border:1px solid var(--line);display:flex;align-items:center;justify-content:center}
.account .order{color:var(--ink);text-decoration:underline;margin-right:14px}
.account .login{color:var(--muted)}
.nav{position:absolute;left:0;top:140px;width:1200px;height:27px;background:var(--navy-deep)}
.nav ul{list-style:none;position:absolute;left:161px;top:0;display:flex;height:27px}
.nav li{height:27px;line-height:27px;color:var(--white);font-size:12.5px;padding:0 24px;border-right:1px solid rgba(255,255,255,.35)}
.nav li:last-child{border-right:none}
.nav li.active{background:var(--red);padding:0 23px;font-size:11.5px}
.hero{position:absolute;left:0;top:167px;width:1200px;height:430px;
  background:linear-gradient(100deg,#aebfe0 0%,#d8e2f3 22%,#9fb6dd 48%,#7f9ccf 70%,#a7bbe0 100%)}
.hero-photo{position:absolute;inset:0}
.caption{position:absolute;left:161px;top:160px;width:357px;height:112px;background:rgba(255,255,255,.9);padding:16px 23px}
.caption h1{font-family:"Roboto Condensed",sans-serif;font-weight:400;font-size:22px;color:var(--navy);line-height:1;white-space:nowrap}
.caption h1 strong{color:var(--red);font-weight:700}
.caption p{font-size:12.5px;line-height:16px;color:var(--ink);margin-top:10px}
.slide-arrow{position:absolute;top:194px;width:43px;height:43px;background:rgba(255,255,255,.85);display:flex;align-items:center;justify-content:center}
.slide-arrow.prev{left:55px}
.slide-arrow.next{left:1098px}
.hero-shade{position:absolute;left:0;top:597px;width:1200px;height:24px;background:linear-gradient(#eeeeee,#ffffff)}
.welcome{position:absolute;left:161px;top:627px;width:360px}
.section-title{font-family:"Roboto Condensed",sans-serif;font-weight:400;font-size:25px;color:var(--navy);line-height:1;white-space:nowrap}
.section-title strong{color:var(--red);font-weight:700}
.welcome .lead{font-size:11.5px;font-weight:700;color:var(--ink);margin-top:22px}
.welcome .body{font-size:11.5px;line-height:17.6px;color:var(--muted);margin-top:5px;width:345px}
.agent-photo{position:absolute;left:530px;top:628px;width:150px;height:222px;border-radius:70px 70px 6px 6px;
  background:linear-gradient(#d9c2ad 0%,#6b5548 30%,#2e2e33 55%,#1d1d22 100%)}
.agent-floor{position:absolute;left:522px;top:846px;width:166px;height:4px;background:radial-gradient(ellipse at center,#999 0%,rgba(255,255,255,0) 70%)}
.divider{position:absolute;left:718px;top:627px;width:1px;height:255px;background:linear-gradient(var(--white),#dcdcdc 20%,#dcdcdc 80%,var(--white))}
.feeds{position:absolute;left:772px;top:627px;width:267px}
.quote{position:relative;margin-top:22px;padding:0 0 0 9px}
.quote-mark{font-family:Georgia,serif;font-size:44px;line-height:1;color:#b4b4b4;position:absolute}
.quote-mark.open{left:0;top:-8px}
.quote-mark.close{right:0;top:94px}
.quote p{font-size:11.5px;line-height:17.6px;color:var(--muted);text-indent:28px}
.quote cite{display:block;font-style:normal;font-size:11.5px;color:var(--muted);margin-top:18px}
.quote cite b{color:var(--ink);font-weight:700}
.read-more{display:inline-block;margin-top:25px;background:var(--red);color:var(--white);font-size:12.5px;padding:5px 11px 6px}
.footer{position:absolute;left:0;top:921px;width:1200px;height:159px;background:var(--navy-deep);color:var(--footer-link)}
.footer ul{list-style:none;position:absolute;top:27px;font-size:11px}
.footer li{height:19.4px;display:flex;align-items:center}
.footer li::before{content:"";width:4px;height:4px;border-radius:50%;background:var(--footer-link);margin-right:9px}
.footer li.current{color:var(--white);text-decoration:underline}
.links-a{left:195px}
.links-b{left:378px}
.f-rule{position:absolute;top:24px;width:1px;height:110px;background:rgba(255,255,255,.25)}
.address{position:absolute;left:536px;top:26px;font-size:11px;line-height:13px;display:flex;gap:10px}
.f-phone{position:absolute;left:536px;top:82px;font-size:16px;font-weight:700;color:var(--white);display:flex;align-items:center;gap:10px}
.f-brand{position:absolute;left:831px;top:20px}
.f-brand .brand-name{color:var(--white)}
.f-brand .main{font-size:34px}
.f-brand .sub{font-size:15px}
.copyright{position:absolute;left:831px;top:84px;font-size:11px;color:var(--footer-link)}
</style>
</head>
<body>
<div class="top-rule"></div>

<header class="header">
  <div class="brand">
    <span class="brand-name"><span class="main">Keystoner</span><span class="sub">4 Real Estate</span></span>
  </div>
  <div class="help">
    <div class="help-label">
      <svg width="13" height="13" viewBox="0 0 24 24"><path fill="#123c8c" d="M6.6 10.8a15.1 15.1 0 0 0 6.6 6.6l2.2-2.2a1 1 0 0 1 1-.25 11.4 11.4 0 0 0 3.6.57 1 1 0 0 1 1 1V20a1 1 0 0 1-1 1A17 17 0 0 1 3 4a1 1 0 0 1 1-1h3.5a1 1 0 0 1 1 1c0 1.25.2 2.45.57 3.57a1 1 0 0 1-.25 1z"/></svg>
      Help Center
    </div>
    <div class="help-phone">555-014-2290</div>
  </div>
  <div class="account">
    <span class="icon-ring"><svg width="14" height="13" viewBox="0 0 24 22"><path fill="none" stroke="#123c8c" stroke-width="2.2" d="M1 2h4l3 12h12l3-9H7"/><circle cx="10" cy="19" r="2" fill="#123c8c"/><circle cx="18" cy="19" r="2" fill="#123c8c"/></svg></span>
    <span class="order">Order Now</span>
    <span class="icon-ring"><svg width="11" height="13" viewBox="0 0 20 24"><path fill="none" stroke="#123c8c" stroke-width="2.6" d="M5 11V7a5 5 0 0 1 10 0v4"/><rect x="2" y="10" width="16" height="13" rx="2" fill="#123c8c"/></svg></span>
    <span class="login">Members Login</span>
  </div>
</header>

<nav class="nav">
  <ul>
    <li class="active">HOME</li>
    <li>WHO WE ARE</li>
    <li>SOLUTIONS</li>
    <li>SERVICES</li>
    <li>F.A.Q</li>
    <li>CONTACT US</li>
  </ul>
</nav>

<section class="hero">
  <div class="hero-photo" role="img" aria-label="Photo of a tall white apartment tower against a cloudy blue sky, with three smiling well-dressed agents holding an open presentation binder"></div>
  <div class="caption">
    <h1>Where Great <strong>Presentations</strong> Begin ...</h1>
    <p>Lorem ipsum dolor sit amet, consectetur adipisicing elit, sed do eiusmod tempor incididunt ut labore et dolore magna aliqua.</p>
  </div>
  <div class="slide-arrow prev"><svg width="14" height="26" viewBox="0 0 14 26"><path d="M12 2 2 13l10 11" fill="none" stroke="#555" stroke-width="1.6"/></svg></div>
  <div class="slide-arrow next"><svg width="14" height="26" viewBox="0 0 14 26"><path d="M2 2l10 11L2 24" fill="none" stroke="#555" stroke-width="1.6"/></svg></div>
</section>
<div class="hero-shade"></div>

<section class="welcome">
  <h2 class="section-title">Welcome to <strong>Keystoner</strong> 4 Real Estate</h2>
  <p class="lead">Your business as an agent is selling real estate.</p>
  <p class="body">Our job is in helping you convert more prospects into serious clients so you can do what you do - sell more real estate. We offer you compelling materials to enable you to create your own personal Listing Presentations; Buyer Presentations; Pre-Listing Packages; Unique Open House Hand-Outs; Handling Objection materials; a "keeping Sellers informed" system; Marketing Newsletter plus Presentation Know-How. Quite literally, we provide everything you need to impress your prospects and out-shine your competition. Keystoner was created by veteran B.C. agents for B.C. agents who truly desire success.</p>
</section>
<div class="agent-photo" role="img" aria-label="Photo of a smiling businesswoman in a dark suit with arms crossed"></div>
<div class="agent-floor"></div>
<div class="divider"></div>

<section class="feeds">
  <h2 class="section-title">Clien`t Feeds</h2>
  <blockquote class="quote">
    <span class="quote-mark open">&ldquo;</span>
    <p>Success in real estate sales is simple. It's in knowing what to say and how to say it – in a manner that people will heed. Everything else Realtors do is secondary, yet… it's the secondary stuff most Realtors focus on, thus, their lack of the success they desire.</p>
    <span class="quote-mark close">&rdquo;</span>
    <cite>-- <b>Dale Morrow</b></cite>
  </blockquote>
  <span class="read-more">Read More</span>
</section>

<footer class="footer">
  <ul class="links-a">
    <li class="current">Home</li>
    <li>What is Keystoner</li>
    <li>Keystoner Demo</li>
    <li>Testimonials</li>
    <li>Free Presentation Tips</li>
    <li>F.A.Q.</li>
  </ul>
  <span class="f-rule" style="left:348px"></span>
  <ul class="links-b">
    <li>Order Keystoner</li>
    <li>Newsletter</li>
    <li>Privacy Policy</li>
    <li>Terms of Use</li>
    <li>Contact Us</li>
  </ul>
  <span class="f-rule" style="left:507px"></span>
  <div class="address">
    <svg width="12" height="17" viewBox="0 0 12 17"><path d="M6 1a5 5 0 0 1 5 5c0 3.5-5 10-5 10S1 9.5 1 6a5 5 0 0 1 5-5z" fill="none" stroke="#c9d6f5" stroke-width="1.5"/><circle cx="6" cy="6" r="1.8" fill="#c9d6f5"/></svg>
    <span>C/o, NORTHGATE AGENT SUPPORT LTD.<br>310 - 48 Harbourline Way<br>Cedar Bay, B.C. X0X 0X0</span>
  </div>
  <div class="f-phone">
    <svg width="14" height="14" viewBox="0 0 24 24"><path fill="#c9d6f5" d="M6.6 10.8a15.1 15.1 0 0 0 6.6 6.6l2.2-2.2a1 1 0 0 1 1-.25 11.4 11.4 0 0 0 3.6.57 1 1 0 0 1 1 1V20a1 1 0 0 1-1 1A17 17 0 0 1 3 4a1 1 0 0 1 1-1h3.5a1 1 0 0 1 1 1c0 1.25.2 2.45.57 3.57a1 1 0 0 1-.25 1z"/></svg>
    555.017.3386
  </div>
  <span class="f-rule" style="left:796px"></span>
  <div class="f-brand">
    <span class="brand-name"><span class="main">Keystoner</span><span class="sub">4 Real Estate</span></span>
  </div>
  <div class="copyright">Copyright © 2014. All Right Reserved</div>
</footer>
</body>
</html>
```